Bold, Modern, Clean "Kestrelwaymassage.com" website

Why we stand out?
We are a male and female mobile massage team. Our names are Paul and Lina. 
Kestrel Way is a Seattle based mobile massage service. Our massage is offered to the community with a goal of facilitating balance within each individual. We specialize in integrated Pain management, and sports/medical massage therapy. Every client's first assessment is attended by our male and female massage therapist team. Depending on the goals identified for an individual determines which therapist will be assigned to provide treatment, if not both.

Our passion...
Here at Kestrel Way, we have a great passion for Postural Resoration and how it is integrated into an individual's Massage treatment. We pride ourselves in being natural facilitators of healing, which takes the ego of the therapist out of the client's healing process. We strive to deliver the best massage possible by including modalities such as Neuromuscular, Myofascial release, spontaneous muscle release, postural restoration, orthopedic, and medical massage.

Our education...

We are both Graduates of Venmora, school of massage therapy. We have continuing education in medical massage, myofacial release, trigger point therapy, postural restoration, anatomy, and spontaneous muscle release. Lina is also a Certified Yoga Instructor, which amplifies her experience with flexibility and strength as it pertains to each individual. Paul's passion is Massage, stretching, and strength training to encourage postural restoration and realignment.

Our rates-

Our rates are $75/ 60 minutes, $95/ 90 minutes, and $120/ 120 minutes.

Education-
Both Lina and I worked as behavioral health professionals that specialized in life skills mentoring for youth who had experienced different types of trauma. This led us both to want to help others in a different environment, where individuals can be empowered to take responsibility over their own healing. To us, massage is a type of manipulation physical therapy, that encourages healing on many levels.

Advice to any massage client-
The most important thing to 'us', as Licenced providers is to get you on to our table to show you our skills. But a good therapist never forgets that it's not about what we do for you, but what we can facilitate for you. Your health and healing has nothing to do with us. It is yours, not ours. Identify what your goals are with any Therapist, and know what the end looks like. Progress should be tangible, such as range of motion, and decreased pain.

Lina and Paul at Kestrel Way are awesome! I recently had open heart surgery, and Lina worked on me to increase my range of motion while helping with the pinched nerve from my arm being in the same position for so long during my surgery. My wife drives a lot for work, and Paul has helped decrease her neck and lower back pain immensely. They are seriously the best therapists I have ever worked with. I would recommend them to anyone who needs anything from stress relief to a medical massage treatment. They are professional, up beat, easy going, and always on time. And, I love that they meet us where ever we like! We did a staycation recently, where they came to our hotel to give us relaxation massages. Although usually they come to our home, where we focus on pain related issues. We will continue to work with them for a long, long time.

Target Market(s)

Mobile massage therapy clients

Industry/Entity Type

Massage Therapy

Coding

Coded - Design and coding required

Number of Pages Required

1 page

Font styles to use
Serif
Sans Serif

Requirements
Must have
• Please add or remove any information that would help the presentation of our website. Our logo is posted below, please include into the website.
• Please include a contact field that includes, kestrelwaymassage@fernmail.net,
• (206) 555-0148
• We have also included our own stock photos, as well as a photo of Paul and Lina. Please include a cropped photo of both massage therapists.

```html
<!DOCTYPE html>
<html lang="en">
<head>
<meta charset="utf-8">
<title>Kestrel Way Mobile Massage</title>
<link href="https://fonts.googleapis.com/css2?family=Roboto:wght@300;400;500;700&display=swap" rel="stylesheet">
<style>
:root{
  --sky-top:#5ccbdc;
  --sky-bottom:#2b9cc4;
  --navy:#0b3c6c;
  --navy-deep:#083050;
  --footer:#0a4566;
  --accent-strip:#1ab4ea;
  --panel:#f1f5f8;
  --ink:#2f3a44;
  --muted:#8a9299;
  --yellow:#f7c21a;
  --green:#9ad82a;
  --teal:#1ec9c2;
  --brand-blue:#1a9fd0;
  --rate-blue:#1a5d8c;
  --star:#f5c400;
}
*{box-sizing:border-box;margin:0;padding:0}
html,body{width:781px;height:1200px;overflow:hidden}
body{position:relative;font-family:'Roboto',sans-serif;color:var(--ink);
  background:linear-gradient(180deg,var(--sky-top) 0%,#45b8d6 50%,var(--sky-bottom) 88%);}
.abs{position:absolute}
.footer-band{left:0;top:1059px;width:781px;height:141px;background:var(--footer)}
.footer-strip{left:0;top:1056px;width:781px;height:5px;background:var(--accent-strip)}

.search{left:64px;top:10px;width:130px;height:24px;border:1px solid #1d5a6e;border-radius:3px;
  font-size:8px;color:#1d3a44;padding:7px 6px}
.search svg{position:absolute;right:5px;top:5px}
.top-phone{left:606px;top:10px;display:flex;align-items:center;gap:8px;font-size:12px;font-weight:500;color:#123}
.top-phone .ring{width:25px;height:25px;border:1px solid #1d4a5a;border-radius:50%;display:flex;align-items:center;justify-content:center}

.nav{left:64px;top:47px;width:653px;height:38px;border-radius:3px;
  background:linear-gradient(180deg,#13477a,var(--navy-deep))}
.nav a{position:absolute;top:14px;font-size:8.5px;font-weight:500;color:#fff;text-decoration:none;letter-spacing:.2px}
.nav a.current{color:var(--yellow)}
.brand{left:342px;top:18px;width:96px;height:96px;border-radius:50%;background:var(--navy);
  border:5px solid #fff;display:flex;align-items:center;justify-content:center;text-align:center;
  font-size:16px;font-weight:700;color:#fff;line-height:1.05}

.hero-photo{left:98px;top:120px;width:430px;height:274px;border-radius:120px 120px 0 0;
  background:radial-gradient(ellipse at 55% 45%,#e9b79b 0%,#d79a7c 40%,rgba(215,154,124,0) 72%)}
.hero-towel{left:64px;top:374px;width:464px;height:20px;background:#f4f4f2;border-radius:8px 8px 0 0}
.arrow{width:25px;height:25px;border:2px solid #fff;border-radius:50%;display:flex;align-items:center;justify-content:center}

.quick{left:535px;top:138px;width:181px;height:196px;background:rgba(232,245,250,.93)}
.quick-head{height:26px;background:var(--brand-blue);color:#fff;font-size:9px;font-weight:500;
  padding:8px 0 0 34px;position:relative}
.quick-head svg{position:absolute;right:6px;top:5px}
.field{position:absolute;left:15px;width:150px;height:24px;border:1px solid #a9c9d6;border-radius:3px;
  background:#f5fafc;font-size:7px;color:#7a8c94;padding:7px 9px}
.submit{position:absolute;left:60px;top:156px;width:61px;height:21px;background:#1e1e1e;border-radius:3px;
  color:#fff;font-size:7.5px;font-weight:500;text-align:center;line-height:21px}

.panel{left:64px;top:394px;width:653px;height:694px;background:var(--panel)}

.card{top:422px;height:142px;width:191px;background:#fff;border-radius:22px 0 22px 0;
  border-top:2px solid;border-bottom:2px solid;box-shadow:0 1px 4px rgba(0,0,0,.08);text-align:center}
.card h3{font-size:14.5px;font-weight:400;color:#222;margin-top:21px}
.card p{font-size:7.2px;line-height:12px;color:var(--muted);margin:8px 10px 0}
.btn-more{display:inline-block;margin-top:12px;width:68px;height:22px;line-height:22px;color:#fff;
  font-size:6.5px;font-weight:700;border-radius:10px 0 10px 0}

.welcome-title{left:86px;top:591px;font-size:20px;font-weight:300;color:#2a2a2a}
.welcome-photo{left:84px;top:634px;width:164px;height:124px;border:2px solid #fff;
  box-shadow:0 0 2px rgba(0,0,0,.2);background:linear-gradient(135deg,#b7aed6 0%,#8f7fb8 55%,#d874b6 100%)}
.welcome-text{left:259px;top:632px;width:234px;font-size:7.4px;line-height:13.4px;color:#3a3a3a;text-align:justify}
.read-more{left:259px;top:746px;font-size:7px;font-style:italic;font-weight:500;color:var(--rate-blue)}

.rates{left:506px;top:597px;width:191px;height:162px;border:1px solid #a9b8c2;border-radius:5px;background:#f3f7f9}
.rates h4{text-align:center;font-size:12.5px;font-weight:400;color:var(--rate-blue);margin-top:9px}
.rate-row{position:absolute;left:16px;display:flex;align-items:center}
.rate-num{width:34px;height:34px;border:1.5px solid var(--rate-blue);display:flex;align-items:center;justify-content:center;
  font-size:16px;color:var(--rate-blue)}
.rate-min{margin-left:7px;width:62px;font-size:12.5px;color:#222;padding:3px 4px}
.rate-min.hl{background:var(--yellow)}
.rate-price{margin-left:12px;font-size:20px;color:var(--rate-blue)}

.dash{left:83px;width:615px;border-top:1px dashed #a8b0b6}
.appt{left:83px;top:793px;font-size:20.5px;font-weight:300;letter-spacing:3px;color:#2a2a2a}
.appt-btn{left:518px;top:790px;width:179px;height:32px;border-radius:4px;background:var(--navy);color:#fff;
  font-size:14px;font-weight:500;text-align:center;line-height:32px}

.tech-photo{top:856px;width:198px;height:120px;border:2px solid #fff;border-bottom:5px solid #0d4e8c;box-shadow:0 0 2px rgba(0,0,0,.15)}
.tech{top:986px;width:198px;text-align:center}
.tech h5{font-size:11.5px;font-weight:400;color:#222}
.stars{font-size:12px;color:var(--star);letter-spacing:1px;margin-top:3px}
.tech p{font-size:7.2px;line-height:12px;color:var(--muted);margin-top:5px}

.f-icon{width:40px;height:40px;border:1.5px solid #4da3c8;border-radius:50%;display:flex;align-items:center;justify-content:center}
.f-text{font-size:7.4px;font-weight:500;color:#fff;line-height:13px}
.social{top:1149px;width:17px;height:17px;border:1px solid #cfe1ea}
</style>
</head>
<body>
<div class="abs footer-band"></div>
<div class="abs footer-strip"></div>

<div class="abs search">Search...
  <svg width="11" height="11" viewBox="0 0 12 12"><circle cx="5" cy="5" r="3.8" fill="none" stroke="#37505a" stroke-width="1.6"/><line x1="8" y1="8" x2="11" y2="11" stroke="#37505a" stroke-width="1.8"/></svg>
</div>
<div class="abs top-phone">
  <span class="ring"><svg width="11" height="11" viewBox="0 0 24 24"><path d="M6.6 10.8c1.4 2.8 3.8 5.1 6.6 6.6l2.2-2.2c.3-.3.7-.4 1-.2 1.1.4 2.3.6 3.6.6.6 0 1 .4 1 1V20c0 .6-.4 1-1 1C10.6 21 3 13.4 3 4c0-.6.4-1 1-1h3.5c.6 0 1 .4 1 1 0 1.3.2 2.5.6 3.6.1.3 0 .7-.2 1z" fill="#1d3a44"/></svg></span>
  (206) 555-0148
</div>

<nav class="abs nav">
  <a class="current" style="left:20px">HOME</a>
  <a style="left:96px">ABOUT US</a>
  <a style="left:188px">SERVICES</a>
  <a style="left:416px">CONSULTANT</a>
  <a style="left:522px">PRICES</a>
  <a style="left:602px">CONTACT</a>
</nav>
<div class="abs brand">KESTREL<br>WAY</div>

<div class="abs hero-photo" role="img" aria-label="Client resting on a massage table with a pink lotus flower"></div>
<div class="abs hero-towel"></div>
<div class="abs arrow" style="left:34px;top:231px"><svg width="12" height="12" viewBox="0 0 12 12"><path d="M10 6H2M5.5 2.5 2 6l3.5 3.5" fill="none" stroke="#fff" stroke-width="1.6"/></svg></div>
<div class="abs arrow" style="left:722px;top:231px"><svg width="12" height="12" viewBox="0 0 12 12"><path d="M2 6h8M6.5 2.5 10 6 6.5 9.5" fill="none" stroke="#fff" stroke-width="1.6"/></svg></div>

<form class="abs quick">
  <div class="quick-head">QUICK CONTACT FORM
    <svg width="20" height="16" viewBox="0 0 20 16"><rect x="1" y="5" width="18" height="10" fill="#fff"/><path d="M1 5l9-4 9 4-9 5z" fill="#fff" stroke="#1a9fd0"/></svg>
  </div>
  <div class="field" style="top:39px">Name :*</div>
  <div class="field" style="top:76px">email :*</div>
  <div class="field" style="top:113px">Phone :*</div>
  <div class="submit">SUBMIT</div>
</form>

<main class="abs panel"></main>

<section class="abs card" style="left:86px;border-color:var(--yellow)">
  <h3>Pain Management</h3>
  <p>There are many variations of passages of Lorem Ipsum available, but the majority have suffered alteration in some form, by injected humour, or randomised words which.</p>
  <span class="btn-more" style="background:var(--yellow)">READ MORE</span>
</section>
<section class="abs card" style="left:297px;border-color:var(--green)">
  <h3>Sports/Medical</h3>
  <p>There are many variations of passages of Lorem Ipsum available, but the majority have suffered alteration in some form, by injected humour, or randomised words which.</p>
  <span class="btn-more" style="background:var(--green)">READ MORE</span>
</section>
<section class="abs card" style="left:506px;border-color:var(--teal)">
  <h3>Mobile Massage</h3>
  <p>There are many variations of passages of Lorem Ipsum available, but the majority have suffered alteration in some form, by injected humour, or randomised words which.</p>
  <span class="btn-more" style="background:var(--teal)">READ MORE</span>
</section>

<h2 class="abs welcome-title">Welcome to Kestrel Way Massage</h2>
<div class="abs welcome-photo" role="img" aria-label="Massage oil bottles beside a pink flower"></div>
<p class="abs welcome-text">We are a male and female mobile massage team. Our names are Paul and Lina. Kestrel Way is a Seattle based mobile massage service. Our massage is offered to the community with a goal of facilitating balance within each individual. We specialize in integrated Pain management, and sports/medical massage therapy. Every client's first assessment is attended by our male and female massage therapist team. Depending on the goals identified for an individual provide treatment, if not both.</p>
<span class="abs read-more">READ MORE</span>

<aside class="abs rates">
  <h4>OUR RATES</h4>
  <div class="rate-row" style="top:32px"><span class="rate-num">60</span><span class="rate-min hl">Minutes.</span><span class="rate-price">$75</span></div>
  <div class="rate-row" style="top:76px"><span class="rate-num">90</span><span class="rate-min">Minutes.</span><span class="rate-price">$95</span></div>
  <div class="rate-row" style="top:119px"><span class="rate-num">120</span><span class="rate-min">Minutes.</span><span class="rate-price">$120</span></div>
</aside>

<div class="abs dash" style="top:784px"></div>
<div class="abs appt">Need to Make an Appointment Now?</div>
<div class="abs appt-btn">contact - (206) 555-0148</div>
<div class="abs dash" style="top:830px"></div>

<div class="abs tech-photo" style="left:83px;background:linear-gradient(135deg,#3a3f46,#d9b49a 60%,#eee)" role="img" aria-label="Therapist working on a client's leg"></div>
<div class="abs tech-photo" style="left:291px;background:linear-gradient(135deg,#e8d2bf,#c99a7e 55%,#a36e55)" role="img" aria-label="Therapist working on a client's back"></div>
<div class="abs tech-photo" style="left:498px;background:linear-gradient(135deg,#f2f2f2,#c8a28a 50%,#6f7378)" role="img" aria-label="Therapist working on a client's hip"></div>

<div class="abs tech" style="left:83px"><h5>Neuromuscular</h5><div class="stars">★★★☆☆</div><p>There are many variations of passages of Lorem Ipsum available, but the majority have suffered alteration in some form, by injected humour.</p></div>
<div class="abs tech" style="left:291px"><h5>Myofascial Release</h5><div class="stars">★★★☆☆</div><p>There are many variations of passages of Lorem Ipsum available, but the majority have suffered alteration in some form, by injected humour.</p></div>
<div class="abs tech" style="left:498px"><h5>Spontaneous Muscle Release</h5><div class="stars">★★★☆☆</div><p>There are many variations of passages of Lorem Ipsum available, but the majority have suffered alteration in some form, by injected humour.</p></div>

<footer>
  <div class="abs f-icon" style="left:66px;top:1120px"><svg width="14" height="18" viewBox="0 0 14 18"><path d="M7 1a6 6 0 0 0-6 6c0 4.5 6 10 6 10s6-5.5 6-10a6 6 0 0 0-6-6z" fill="#4da3c8"/><circle cx="7" cy="7" r="2.2" fill="#0a4566"/></svg></div>
  <div class="abs f-text" style="left:118px;top:1127px">41/207 Marlow Street 120,<br>Chicago.IL 60699-234</div>

  <div class="abs f-icon" style="left:306px;top:1120px"><svg width="15" height="15" viewBox="0 0 24 24"><path d="M6.6 10.8c1.4 2.8 3.8 5.1 6.6 6.6l2.2-2.2c.3-.3.7-.4 1-.2 1.1.4 2.3.6 3.6.6.6 0 1 .4 1 1V20c0 .6-.4 1-1 1C10.6 21 3 13.4 3 4c0-.6.4-1 1-1h3.5c.6 0 1 .4 1 1 0 1.3.2 2.5.6 3.6.1.3 0 .7-.2 1z" fill="#4da3c8"/></svg></div>
  <div class="abs f-text" style="left:359px;top:1127px">Telephone : (206) 555-0148<br>E mail :Kestrelwaymassage.com</div>

  <div class="abs f-icon" style="left:554px;top:1120px"><svg width="16" height="12" viewBox="0 0 16 12"><rect x="0" y="0" width="16" height="12" rx="1.5" fill="#4da3c8"/><path d="M1 1l7 5.5L15 1" fill="none" stroke="#0a4566" stroke-width="1.4"/></svg></div>
  <div class="abs f-text" style="left:606px;top:1127px">kestrelway 2015 | Privacy Policy</div>
  <div class="abs social" style="left:608px"></div>
  <div class="abs social" style="left:634px"></div>
  <div class="abs social" style="left:659px"></div>
  <div class="abs social" style="left:686px"></div>
</footer>
</body>
</html>
```